Moravel Aesthetic Doctor

I require an elegant, luxurious looking business card for my aesthetic business. I am a doctor and that will set me aside from competitors. I am planning to provide home and spa based treatments to clients with high expectations. I have attached my logo.

```html
<!DOCTYPE html>
<html lang="en">
<head>
<meta charset="utf-8">
<title>Moravel Aesthetic Doctor – Business Card</title>
<link href="https://fonts.googleapis.com/css2?family=Montserrat:wght@300;400;500&display=swap" rel="stylesheet">
<style>
  :root {
    --bg: #dcdde1;
    --blue-dark: #2a7bbb;
    --blue-light: #4aa4da;
    --blue-text: #2f80c3;
    --sky: #a9d6f0;
    --white: #ffffff;
    --paper: #f7f7f8;
    --ink: #3a3d42;
    --rule: #3a8fd0;
  }
  * { margin: 0; padding: 0; box-sizing: border-box; }
  html, body { width: 1200px; height: 800px; overflow: hidden; }
  body {
    background: var(--bg);
    font-family: "Montserrat", Arial, sans-serif;
    position: relative;
  }
  .card {
    position: absolute;
    left: 389px;
    width: 460px;
    height: 263px;
  }
  .card--front {
    top: 93px;
    background: linear-gradient(200deg, var(--blue-light) 0%, var(--blue-dark) 100%);
    color: var(--white);
  }
  .card--back {
    top: 422px;
    background: linear-gradient(160deg, var(--white) 0%, var(--paper) 100%);
    color: var(--ink);
  }
  .brand { position: absolute; display: flex; align-items: center; }
  .brand__dot { border-radius: 50%; flex: none; }
  .brand__name {
    font-weight: 400;
    text-transform: uppercase;
    line-height: 1;
  }
  .brand__name span { display: block; }
  .card--front .brand { left: 76px; top: 66px; gap: 18px; }
  .card--front .brand__dot { width: 70px; height: 70px; background: var(--sky); }
  .card--front .brand__name { color: var(--white); }
  .card--front .brand__word { font-size: 42px; letter-spacing: 2px; }
  .card--front .brand__sub { font-size: 17px; letter-spacing: 1.4px; margin-top: 7px; }
  .card--back .brand { right: 26px; top: 30px; gap: 10px; }
  .card--back .brand__dot { width: 54px; height: 54px; background: var(--sky); }
  .card--back .brand__name { color: var(--blue-text); }
  .card--back .brand__word { font-size: 31px; letter-spacing: 1.5px; }
  .card--back .brand__sub { font-size: 12.5px; letter-spacing: 1px; margin-top: 5px; }
  .services {
    position: absolute;
    left: 0; right: 0; top: 186px;
    text-align: center;
    font-weight: 300;
  }
  .services__list { font-size: 11px; line-height: 13.5px; }
  .services__tagline { font-size: 14.5px; font-weight: 400; margin-top: 4px; }
  .person { position: absolute; left: 25px; top: 150px; }
  .person__name { font-size: 13px; font-weight: 500; color: var(--blue-text); }
  .person__post { font-size: 7px; font-weight: 500; color: var(--ink); margin-left: 2px; }
  .person__title { font-size: 11px; margin-top: 2px; }
  .divider {
    position: absolute; left: 25px; width: 409px; top: 191px;
    height: 1px; background: var(--rule);
  }
  .contacts { position: absolute; left: 25px; top: 197px; list-style: none; font-size: 11px; }
  .contacts li { display: flex; align-items: center; gap: 6px; height: 13.5px; }
  .contacts svg { width: 8px; height: 8px; fill: var(--blue-text); }
  .social { position: absolute; right: 26px; top: 207px; text-align: right; }
  .social__label { font-size: 11px; color: var(--ink); }
  .social__icons { display: flex; gap: 6px; justify-content: flex-end; margin-top: 7px; }
  .social__icon { width: 8px; height: 8px; border-radius: 50%; background: var(--blue-text); }
</style>
</head>
<body>
  <section class="card card--front">
    <div class="brand">
      <div class="brand__dot"></div>
      <div class="brand__name">
        <span class="brand__word">Moravel</span>
        <span class="brand__sub">Aesthetic Doctor</span>
      </div>
    </div>
    <div class="services">
      <p class="services__list">Dermal injectables - Plasma facials - Microneedling<br>Skin boosters - Excessive sweating</p>
      <p class="services__tagline">Home and Spa Based Treatments</p>
    </div>
  </section>

  <section class="card card--back">
    <div class="brand">
      <div class="brand__dot"></div>
      <div class="brand__name">
        <span class="brand__word">Moravel</span>
        <span class="brand__sub">Aesthetic Doctor</span>
      </div>
    </div>
    <div class="person">
      <p><span class="person__name">Dr Elena Varga</span><span class="person__post">MRCPCH MD</span></p>
      <p class="person__title">Australasian Diploma of Aesthetic Medicine</p>
    </div>
    <div class="divider"></div>
    <ul class="contacts">
      <li><svg viewBox="0 0 10 10"><path d="M2 0.5 L3.8 0.5 L4.3 3 L3 3.8 C3.6 5.2 4.8 6.4 6.2 7 L7 5.7 L9.5 6.2 L9.5 8 C9.5 9 8.8 9.5 8 9.5 C4 9.2 0.8 6 0.5 2 C0.5 1.2 1 0.5 2 0.5Z"/></svg>0800 555 014</li>
      <li><svg viewBox="0 0 10 10"><path d="M0.5 2 H9.5 V8.5 H0.5Z M1 2.5 L5 5.5 L9 2.5" fill="none" stroke="#2f80c3" stroke-width="1"/></svg>elena@moravel.co.nz</li>
      <li><svg viewBox="0 0 10 10"><g fill="none" stroke="#2f80c3" stroke-width="0.9"><circle cx="5" cy="5" r="4.4"/><ellipse cx="5" cy="5" rx="2" ry="4.4"/><path d="M0.6 5 H9.4 M1.3 2.8 H8.7 M1.3 7.2 H8.7"/></g></svg>www.moravel.co.nz</li>
    </ul>
    <div class="social">
      <p class="social__label">follow</p>
      <div class="social__icons">
        <span class="social__icon"></span>
        <span class="social__icon"></span>
      </div>
    </div>
  </section>
</body>
</html>
```